Client website

Our designer we were working with had some personal things come up and was unable to finish the design for the site.

We have a .psd file started, and will be attaching it to the project.
Updates

Reason: I still want to polish the designs with the current designer and allow more designers the opportunity to participate.

Reason: I'm extending the deadline for another day to give everyone enough time for the final changes our client wants.

I'm trying to extend the deadline so we can get one last set of comps in for my client.  Could everyone message me and let me know how much time they need to do the final tweaks?

Reason: Hey everyone.  I've been sick the last 3 days and I haven't been able to provide feedback on designs.  I'm extending just a few more days so I can catch up here.  Thanks everyone for your patience.

Target Market(s)

Adults in United States aged 25 to 60 that handle the household budgets and maintenance.

Requirements
Must have
• 1) We need 2 pages. 1 page for flood restoration, 1 page for carpet cleaning

2) The 1-800-# must be the focal point of the website for both pages. People are mostly looking to contact someone ASAP to get them out to their house when flooding occurs.

3) We''re going to have a slide show area to high-light different sub-services offered for each page.

4) We really want a chatterbook / plinker feed area. We''re going to use chatterbook for special offers, and plinker for weather updates. The chatterbook feed is going to be on the carpet cleaning page. The plinker feed is going to be on the flood page.

5) We want an SEO text sections near the bottom.

6) The very bottom will link to the privacy policy and user agreement as well as company name and copyright details.

We really want to stick to the say "theme" that our first designer started with.
Nice to have
• I'm not a designer, so if you think something looks better somewhere, or something can be eliminated, or something can be enhanced, but all means, let us know.

```html
<!DOCTYPE html>
<html lang="en">
<head>
<meta charset="utf-8">
<title>Pure-Rinse — Water &amp; Fire Damage Restoration</title>
<link rel="stylesheet" href="https://fonts.googleapis.com/css2?family=PT+Sans:wght@400;700&family=Indie+Flower&family=Arimo:wght@400;700&display=swap">
<style>
  :root {
    --backdrop: #1c2a36;
    --page-top: #8fd0f2;
    --page-mid: #3f8cc9;
    --page-deep: #163a60;
    --page-edge: #1877d4;
    --brand-square: #1fa23f;
    --brand-text: #1f5f98;
    --title-blue: #2379b8;
    --panel-hi: #e8f3fa;
    --panel-lo: #c3d6e6;
    --card: #c9d6e2;
    --card-hi: #dbe5ee;
    --text: #555c63;
    --text-soft: #5c636a;
    --nav-blue: #2a9be0;
    --nav-green: #1fb03c;
    --note: #eeeadc;
    --footer: #c4ccd4;
  }
  * { box-sizing: border-box; margin: 0; padding: 0; }
  html, body { width: 1200px; height: 1200px; overflow: hidden; }
  body {
    position: relative;
    background: radial-gradient(ellipse at center, #26384a 0%, var(--backdrop) 70%);
    font-family: "Arimo", Arial, sans-serif;
    color: var(--text);
  }
  .page {
    position: absolute; left: 135px; top: 0; width: 933px; height: 1200px;
    background: linear-gradient(180deg, #cfeaf8 0%, var(--page-top) 30%, var(--page-mid) 58%, #24578c 82%, var(--page-deep) 100%);
    border-left: 4px solid var(--page-edge);
    border-right: 4px solid var(--page-edge);
    box-shadow: 0 0 40px rgba(0,0,0,.6);
  }
  .header-scene {
    position: absolute; left: 0; top: 0; width: 100%; height: 315px;
    background: linear-gradient(180deg, #3d8fe0 0%, #8cc9f2 35%, #d8f0fb 70%, #c5e6f7 100%);
  }
  .wave {
    position: absolute; left: 0; top: 110px; width: 100%; height: 200px;
    background: linear-gradient(180deg, rgba(120,190,235,.55), rgba(200,235,250,.1));
  }
  .brand {
    position: absolute; left: 48px; top: 210px;
    display: flex; align-items: center; gap: 12px;
  }
  .brand-square { width: 30px; height: 30px; background: var(--brand-square); flex: none; }
  .brand-name {
    font-family: "PT Sans", sans-serif; font-weight: 700; font-size: 36px;
    color: var(--brand-text); line-height: 1;
  }
  .brand-tag {
    position: absolute; left: 58px; top: 250px;
    font-family: "PT Sans", sans-serif; font-weight: 700; font-size: 13px;
    color: var(--brand-text);
  }
  .nav {
    position: absolute; left: 1px; top: 315px; display: flex; list-style: none;
  }
  .nav li {
    width: 147px; height: 35px; line-height: 36px; text-align: center;
    font-family: "Arimo", sans-serif; font-size: 16px; letter-spacing: 1px; color: #fff;
    background: linear-gradient(180deg, #4fb8f0, var(--nav-blue));
    border-right: 1px solid rgba(255,255,255,.7);
  }
  .nav li.is-active { background: linear-gradient(180deg, #3cc956, var(--nav-green)); }
  .call-note {
    position: absolute; left: 905px; top: 185px; width: 210px; height: 190px;
    background: linear-gradient(160deg, #f6f3e8, var(--note));
    transform: rotate(25deg);
    box-shadow: 4px 6px 12px rgba(0,0,0,.35), 8px 10px 0 -2px #ddd7c4;
    font-family: "Indie Flower", cursive; color: #333; padding: 30px 10px 0 14px;
  }
  .call-note .pin {
    position: absolute; left: 40px; top: -4px; width: 22px; height: 22px;
    border-radius: 50%; background: #23b93c;
  }
  .call-note .call { font-size: 33px; line-height: 1.1; white-space: nowrap; }
  .call-note .phone { font-size: 25px; margin-top: 8px; white-space: nowrap; }
  .slider {
    position: absolute; left: 178px; top: 395px; width: 844px; height: 297px;
    border-radius: 14px;
    background: linear-gradient(180deg, var(--panel-hi), var(--panel-lo));
    box-shadow: 0 3px 6px rgba(0,0,0,.25);
    padding: 40px 44px 40px 48px;
  }
  .slider h1 {
    font-family: "PT Sans", sans-serif; font-weight: 700; font-size: 53px;
    color: var(--title-blue); letter-spacing: -2px; line-height: 1; margin-left: -4px;
  }
  .slider p { width: 470px; font-size: 16px; line-height: 18px; margin-top: 18px; }
  .slider p:first-of-type { margin-top: 40px; }
  .slider .cta {
    position: absolute; left: 613px; top: 171px; width: 177px; height: 44px;
    border-radius: 8px; background: linear-gradient(180deg, #3fd05a, #0f9a2c);
    color: #fff; font-family: "PT Sans", sans-serif; font-weight: 700; font-size: 22px;
    text-align: center; line-height: 44px; letter-spacing: -.5px;
    box-shadow: 0 2px 4px rgba(0,0,0,.3);
  }
  .slide-arrow { position: absolute; top: 522px; width: 45px; height: 45px; }
  .slide-arrow.prev { left: 155px; }
  .slide-arrow.next { left: 998px; }
  .feed {
    position: absolute; width: 400px; height: 172px; border-radius: 8px;
    background: linear-gradient(180deg, var(--card-hi), var(--card));
    box-shadow: 0 3px 6px rgba(0,0,0,.3);
  }
  .feed.chatterbook { left: 178px; top: 733px; }
  .feed.plinker { left: 621px; top: 736px; }
  .feed .badge {
    position: absolute; left: 43px; top: 38px; width: 64px; height: 64px;
    border-radius: 6px; background: linear-gradient(180deg, #8ab0d8, #4f78ad);
  }
  .feed.plinker .badge { left: 35px; background: linear-gradient(180deg, #f4f6f8, #c8d0d8); }
  .feed .follow {
    position: absolute; left: 35px; top: 113px; width: 81px; height: 21px;
    background: #fafafa; border: 1px solid #aaa; font-size: 11px; color: #222;
    text-align: center; line-height: 20px;
  }
  .feed.plinker .follow { left: 26px; }
  .feed h2 {
    position: absolute; left: 142px; top: 28px;
    font-family: "PT Sans", sans-serif; font-weight: 700; font-size: 31px;
    color: var(--title-blue); letter-spacing: -1px;
  }
  .feed.plinker h2 { left: 136px; }
  .feed p {
    position: absolute; left: 142px; top: 70px; width: 235px;
    font-size: 12.5px; line-height: 15px; color: var(--text-soft);
  }
  .feed.plinker p { left: 135px; }
  .seo {
    position: absolute; top: 954px; width: 262px; height: 92px; border-radius: 4px;
    background: linear-gradient(180deg, var(--card-hi), var(--card));
    box-shadow: 0 3px 6px rgba(0,0,0,.3);
    padding: 16px 30px 0 28px; font-size: 10.5px; line-height: 15px; color: var(--text-soft);
  }
  .seo.one { left: 178px; }
  .seo.two { left: 470px; }
  .seo.three { left: 759px; }
  .diver {
    position: absolute; left: 885px; top: 1040px; width: 125px; height: 48px;
    border-radius: 20px; background: radial-gradient(ellipse, rgba(80,190,120,.7), rgba(30,80,90,0) 70%);
  }
  .site-footer {
    position: absolute; left: 178px; top: 1091px; width: 844px; height: 36px;
    background: linear-gradient(180deg, #d3d9df, var(--footer));
    box-shadow: 0 3px 6px rgba(0,0,0,.3);
    display: flex; justify-content: space-between; align-items: center;
    padding: 0 37px 0 28px; font-size: 11px; color: #111;
  }
</style>
</head>
<body>
  <div class="page">
    <div class="header-scene" role="img" aria-label="Bright sky with clouds and a splashing water wave">
      <div class="wave"></div>
    </div>
    <div class="brand">
      <span class="brand-square"></span>
      <span class="brand-name">Pure-Rinse</span>
    </div>
    <div class="brand-tag">Water &amp; Fire Damage Restoration</div>
    <ul class="nav">
      <li class="is-active">home</li>
      <li>about</li>
      <li>services</li>
      <li>faq</li>
      <li>contact</li>
    </ul>
  </div>

  <div class="call-note">
    <span class="pin"></span>
    <div class="call">Call Us Now!</div>
    <div class="phone">1-800-5550-1937!</div>
  </div>

  <section class="slider">
    <h1>Sub-service Number One</h1>
    <p>Lorem ipsum dolor sit amet, consectetur adipiscing elit. Duis semper, turpis in sodales ultricies, felis dui facilisis sem, nec dignissim augue nisl eu eros. Sed a faucibus massa.</p>
    <p>Suspendisse id felis tellus, vel sagittis sem. Fusce aliquam scelerisque diam et tempor.</p>
    <a class="cta">A Button »</a>
  </section>

  <svg class="slide-arrow prev" viewBox="0 0 45 45" aria-label="Previous slide">
    <circle cx="22.5" cy="22.5" r="21" fill="#1a8ee0" stroke="#e8f4fb" stroke-width="2"/>
    <path d="M22 15 L15 22.5 L22 30 M30 15 L23 22.5 L30 30" fill="none" stroke="#fff" stroke-width="3"/>
  </svg>
  <svg class="slide-arrow next" viewBox="0 0 45 45" aria-label="Next slide">
    <circle cx="22.5" cy="22.5" r="21" fill="#1a8ee0" stroke="#e8f4fb" stroke-width="2"/>
    <path d="M15 15 L22 22.5 L15 30 M23 15 L30 22.5 L23 30" fill="none" stroke="#fff" stroke-width="3"/>
  </svg>

  <section class="feed chatterbook">
    <span class="badge"></span>
    <span class="follow">Follow us!</span>
    <h2>Chatterbook Feed</h2>
    <p>- Lorem ipsum dolor sit amet, consectetur adipiscing elit. Duis semper, turpis in sodales ultricies, felis dui facilisis sem, nec dignissim</p>
  </section>
  <section class="feed plinker">
    <span class="badge"></span>
    <span class="follow">Follow us!</span>
    <h2>Plinker Feed</h2>
    <p>- Lorem ipsum dolor sit amet, consectetur adipiscing elit. Duis semper, turpis in sodales ultricies, felis dui facilisis sem, nec dignissim</p>
  </section>

  <div class="seo one">- Lorem ipsum dolor sit amet, consectetur adipiscing elit. Duis semper, turpis in sodales ultricies, felis dui facilisis sem, nec dignissim</div>
  <div class="seo two">- Lorem ipsum dolor sit amet, consectetur adipiscing elit. Duis semper, turpis in sodales ultricies, felis dui facilisis sem, nec dignissim</div>
  <div class="seo three">- Lorem ipsum dolor sit amet, consectetur adipiscing elit. Duis semper, turpis in sodales ultricies, felis dui facilisis sem, nec dignissim</div>

  <div class="diver" role="img" aria-label="Small scuba diver swimming underwater"></div>

  <footer class="site-footer">
    <span>Copyright 2010. Pure-Rinse.</span>
    <span>Privacy Policy | User Agreement</span>
  </footer>
</body>
</html>
```